New design for Giftwell Hub Website - landing page plus 3 carousel pages

We have a new website we want to launch for 501c3 organizations - Faith-based organizations, not for profit organizations, colleges and universities. Note - this is a design only project. We want to see designs for the landing page and the 3 other pages - Faith-based organizations, not for profit organizations, colleges and universities.
Format: We expect to create this website in Wix so requirement is to make the graphics Wix compatible
See Dossier attached for more details, 4 wireframes (1 landing page and 3 carousel pages), and brand guidelines
Please be creative and and make the visuals engaging. We do NOT want you to simply replicate what is in the wireframe. We are looking for a totally new, fresh and engaging design.
Number of Pages Required
1 page
Look and feel
Each slider illustrates characteristics of the customer's brand and the style your logo design should communicate.

```html
<!DOCTYPE html>
<html lang="en">
<head>
<meta charset="utf-8">
<title>Giftwell Hub – 501C3 Giving</title>
<link rel="stylesheet" href="https://fonts.googleapis.com/css2?family=Poppins:wght@300;400;500;600;700&display=swap">
<style>
:root{
  --navy:#051a3b;
  --navy-2:#0b2551;
  --teal:#0a8f9b;
  --teal-dark:#057f8a;
  --green:#00c48c;
  --green-line:#15c38a;
  --white:#ffffff;
  --soft:#dbe6f3;
  --yellow:#fbbf10;
  --blue:#4aa3e8;
  --red:#e0524a;
  --card-grey:#c9d2dc;
}
*{margin:0;padding:0;box-sizing:border-box}
html,body{width:1200px;height:3830px;overflow:hidden}
body{background:var(--navy);font-family:'Poppins',sans-serif;color:var(--white);position:relative}
.abs{position:absolute}
.center{left:0;width:1200px;text-align:center}
svg{display:block}

/* header */
.brand{display:flex;align-items:center;gap:10px;font-weight:500;font-size:28px;color:var(--white)}
.brand-dot{width:40px;height:40px;border-radius:50%;border:4px solid var(--white);flex:none}
.site-header .brand{left:112px;top:26px}
.nav{left:400px;top:39px;display:flex;gap:22px;font-size:14px;font-weight:600}
.nav a{color:var(--white);text-decoration:none}
.nav a.active{color:var(--green);border-bottom:2px solid var(--green);padding-bottom:4px}
.login{left:974px;top:30px;width:112px;height:40px;border-radius:20px;background:var(--teal);font-size:14px;font-weight:600;display:flex;align-items:center;justify-content:center;gap:7px}

.glow{border-radius:50%;filter:blur(40px);opacity:.35;background:var(--green)}

h1,h2{font-weight:700;letter-spacing:.5px}
.hero-title{top:232px;font-size:54px}
.hero-sub{top:310px;font-size:16px;line-height:26px;color:var(--soft)}
.org{width:180px;text-align:center}
.org-ring{width:141px;height:141px;border-radius:50%;background:var(--white);border:5px solid var(--green);margin:0 auto;display:flex;align-items:center;justify-content:center}
.org-name{margin-top:16px;font-size:20px;font-weight:600;line-height:26px}

.process-title{top:845px;font-size:52px}
.step{width:215px}
.step-badge{width:129px;height:129px;border-radius:50%;display:flex;align-items:center;justify-content:center}
.step-label{display:inline-block;background:var(--navy-2);border-radius:14px;padding:4px 18px;font-size:14px;font-weight:600;margin:18px 0 12px}
.step p{font-size:15px;line-height:25.5px;color:var(--soft)}
.btn{display:flex;align-items:center;justify-content:center;border-radius:22px;font-weight:600;font-size:14px}
.btn-teal{background:var(--teal)}
.btn-green{background:var(--green)}

.donation{left:0;top:1465px;width:1200px;height:542px;background:var(--navy-2)}
.donation-title{top:1545px;font-size:52px}
.donation-note{top:1620px;font-size:16px;font-weight:600}
.donation-want{top:1656px;font-size:16px;font-weight:600;color:var(--green)}
.amounts{left:109px;top:1707px;display:flex;gap:7px}
.amount{width:158px;height:73px;border:3px solid var(--green);border-radius:4px;display:flex;align-items:center;justify-content:center;font-size:36px;font-weight:600;color:var(--green)}
.amount.other{background:var(--green);color:var(--white);font-size:15px;line-height:25px;text-align:center}
.cards{left:431px;top:1808px;display:flex;gap:6px}
.card-shape{width:63px;height:33px;background:var(--white);border-radius:3px;position:relative}
.card-shape::before{content:"";position:absolute;left:10px;top:9px;width:14px;height:10px;border-radius:2px;background:var(--card-grey)}
.card-shape::after{content:"";position:absolute;left:10px;right:10px;bottom:7px;height:3px;border-radius:2px;background:var(--card-grey)}

.donate-box{top:2110px;width:477px;height:410px;background:var(--teal);text-align:center}
.donate-icon{width:115px;height:115px;border-radius:50%;background:var(--white);margin:31px auto 0;display:flex;align-items:center;justify-content:center}
.donate-box h3{font-size:17px;font-weight:600;margin-top:30px}
.donate-box small{display:block;font-size:12px;margin-top:6px}
.donate-box .brand{justify-content:center;margin-top:22px;font-size:30px}
.donate-box .btn{width:166px;height:42px;margin:26px auto 0}

.video{left:112px;top:2625px;width:976px;height:426px;border-radius:14px;background:linear-gradient(135deg,#6b6257,#3b3a36 55%,#8d8577)}
.play{left:575px;top:2812px;width:52px;height:52px;border-radius:50%;background:var(--green);display:flex;align-items:center;justify-content:center}

.enroll{left:0;top:3155px;width:600px;height:555px;background:var(--teal-dark)}
.notify{left:600px;top:3155px;width:600px;height:555px;background:var(--green)}
.enroll-title{left:110px;top:3218px;font-size:32px;font-weight:700}
.perk{left:112px;display:flex;gap:15px}
.perk-icon{width:78px;height:78px;border-radius:50%;background:var(--green);flex:none;display:flex;align-items:center;justify-content:center}
.perk h4{font-size:16px;font-weight:700;margin-top:2px}
.perk p{font-size:15px;line-height:25px;color:var(--soft);margin-top:4px}
.notify-title{left:680px;top:3218px;font-size:32px;font-weight:700;line-height:39px}
.subscribe{left:680px;top:3317px;width:440px;height:48px;background:var(--white);border-radius:24px;display:flex;align-items:center;justify-content:space-between;padding-left:26px;font-size:14px;color:#6a7380}
.subscribe span.btn{width:154px;height:44px;margin-right:2px;background:var(--teal-dark);color:var(--white)}
.never{left:680px;top:3385px;font-size:36px;font-weight:300}
.notify-text{left:680px;width:440px;font-size:15px;line-height:25.5px}
.footer{top:3755px;font-size:15px}
.footer-code{left:1128px;top:3758px;font-size:12px}
</style>
</head>
<body>

<div class="abs glow" style="left:950px;top:-40px;width:260px;height:160px"></div>
<div class="abs glow" style="left:40px;top:560px;width:140px;height:120px"></div>

<header class="site-header">
  <div class="abs brand"><span class="brand-dot"></span>Giftwell Hub</div>
  <nav class="abs nav">
    <a class="active" href="#">HOME</a><a href="#">ABOUT US</a><a href="#">NEWSROOM</a><a href="#">PATENTS</a><a href="#">CLIENTS</a><a href="#">FAQ</a><a href="#">CONTACT</a>
  </nav>
  <div class="abs login"><svg width="11" height="13" viewBox="0 0 11 13"><circle cx="5.5" cy="3.5" r="3" fill="#fff"/><path d="M0 13 Q0 7 5.5 7 Q11 7 11 13 Z" fill="#fff"/></svg>LOGIN</div>
</header>

<section class="intro">
  <h1 class="abs center hero-title">501C3 ORGANIZATION</h1>
  <p class="abs center hero-sub">Lorem ipsum dolor sit amet, consectetur adipiscing elit, sed do eiusmod tempor<br>incididunt ut labore et dolore magna aliqua</p>
  <div class="abs org" style="left:274px;top:394px">
    <div class="org-ring" aria-label="Non profit organization icon">
      <svg width="76" height="76" viewBox="0 0 76 76" fill="none" stroke="#0fa88a" stroke-width="8" stroke-linecap="round">
        <path d="M38 8 Q58 20 46 36"/><path d="M68 38 Q56 58 40 46"/><path d="M38 68 Q18 56 30 40"/><path d="M8 38 Q20 18 36 30"/>
      </svg>
    </div>
    <div class="org-name">Non Profit<br>Organization</div>
  </div>
  <div class="abs org" style="left:511px;top:394px">
    <div class="org-ring" aria-label="Faith base icon">
      <svg width="100" height="100" viewBox="0 0 100 100">
        <circle cx="50" cy="50" r="42" fill="#0b2a45"/>
        <path d="M50 8 A42 42 0 0 1 92 50 L70 50 A20 20 0 0 0 50 30 Z" fill="#00c48c"/>
        <path d="M50 92 A42 42 0 0 1 8 50 L30 50 A20 20 0 0 0 50 70 Z" fill="#00c48c"/>
        <circle cx="50" cy="50" r="20" fill="#fff"/>
        <path d="M26 60 v16 M20 66 h12" stroke="#fff" stroke-width="3"/>
        <path d="M74 22 l3 6 6 1 -5 4 1 6 -5 -3 -5 3 1 -6 -5 -4 6 -1 z" fill="#fff"/>
      </svg>
    </div>
    <div class="org-name">Faith Base</div>
  </div>
  <div class="abs org" style="left:746px;top:394px">
    <div class="org-ring" aria-label="Graduation cap icon">
      <svg width="80" height="80" viewBox="0 0 80 80" fill="#0fa88a">
        <path d="M40 6 L74 20 L40 34 L6 20 Z"/>
        <path d="M20 27 V40 Q40 50 60 40 V27 L40 36 Z"/>
        <path d="M70 22 V38" stroke="#0fa88a" stroke-width="3"/>
        <path d="M10 78 V66 Q10 54 24 54 H56 Q70 54 70 66 V78 Z"/>
      </svg>
    </div>
    <div class="org-name">Colleges and<br>Universities</div>
  </div>
  <svg class="abs" style="left:0;top:640px" width="1200" height="110" viewBox="0 0 1200 110">
    <defs><linearGradient id="band" x1="0" x2="1"><stop offset="0" stop-color="#0a8f9b"/><stop offset="1" stop-color="#00c48c"/></linearGradient></defs>
    <path d="M0 14 Q600 160 1200 14 L1200 28 Q600 180 0 28 Z" fill="url(#band)"/>
  </svg>
</section>

<section class="process">
  <h2 class="abs center process-title">OUR PROCESS</h2>
  <svg class="abs" style="left:0;top:900px" width="1200" height="200" viewBox="0 0 1200 200">
    <path d="M90 25 Q110 80 170 100 Q260 180 380 180 M500 160 Q560 80 640 85 M740 110 Q800 170 880 170 M1000 135 Q1035 110 1040 80" fill="none" stroke="#fff" stroke-width="2" stroke-dasharray="5 6"/>
  </svg>
  <div class="abs step" style="left:111px;top:944px">
    <div class="step-badge" style="background:var(--green-line)" aria-label="Settings screen icon">
      <svg width="66" height="66" viewBox="0 0 66 66" fill="none" stroke="#fff" stroke-width="2.5">
        <rect x="6" y="20" width="54" height="36" rx="3"/><path d="M26 62 h14 M33 56 v6"/>
        <circle cx="33" cy="38" r="8"/><path d="M33 26 v4 M33 46 v4 M21 38 h4 M41 38 h4"/>
        <path d="M14 20 v-10 M33 20 v-12 M52 20 v-10"/><circle cx="14" cy="8" r="3"/><circle cx="33" cy="5" r="3"/><circle cx="52" cy="8" r="3"/>
      </svg>
    </div>
    <span class="step-label">STEP 1</span><p>Lorem ipsum dolor sit amet, consectetur adipiscing elit, sed do eiusmod tempor inci didunt ut labore</p>
  </div>
  <div class="abs step" style="left:368px;top:996px">
    <div class="step-badge" style="background:var(--blue)" aria-label="Data flow icon">
      <svg width="66" height="66" viewBox="0 0 66 66" fill="none" stroke="#fff" stroke-width="2.5">
        <path d="M30 8 v50"/><circle cx="10" cy="22" r="4"/><circle cx="10" cy="42" r="4"/><path d="M14 22 h16 M14 42 h16 M4 32 h26"/>
        <path d="M30 16 h14 M30 33 h14 M30 50 h14"/><circle cx="52" cy="16" r="7"/><circle cx="52" cy="33" r="7"/><circle cx="52" cy="50" r="7"/>
      </svg>
    </div>
    <span class="step-label">STEP 2</span><p>Lorem ipsum dolor sit amet, consectetur adipiscing elit, sed do eiusmod tempor inci didunt ut labore</p>
  </div>
  <div class="abs step" style="left:624px;top:944px">
    <div class="step-badge" style="background:var(--yellow)" aria-label="Network screen icon">
      <svg width="66" height="66" viewBox="0 0 66 66" fill="none" stroke="#fff" stroke-width="2.5">
        <rect x="6" y="8" width="54" height="38" rx="3"/><path d="M6 38 h54 M24 56 h18 M33 46 v10"/>
        <rect x="14" y="15" width="18" height="14"/><path d="M38 18 h14 M38 24 h14"/>
        <circle cx="44" cy="44" r="6" fill="#fbbf10"/><circle cx="56" cy="54" r="5" fill="#fbbf10"/><circle cx="36" cy="58" r="5" fill="#fbbf10"/><path d="M48 48 l4 3 M40 49 l-2 4"/>
      </svg>
    </div>
    <span class="step-label">STEP 3</span><p>Lorem ipsum dolor sit amet, consectetur adipiscing elit, sed do eiusmod tempor inci didunt ut labore</p>
  </div>
  <div class="abs step" style="left:881px;top:996px">
    <div class="step-badge" style="background:var(--red)" aria-label="Devices icon">
      <svg width="66" height="66" viewBox="0 0 66 66" fill="none" stroke="#fff" stroke-width="2.5">
        <rect x="4" y="8" width="50" height="34" rx="3"/><path d="M4 34 h50 M20 50 h18 M29 42 v8"/>
        <path d="M10 28 l10 -10 8 8 6 -6 8 8"/><circle cx="42" cy="16" r="3"/>
        <rect x="44" y="28" width="18" height="32" rx="3" fill="#e0524a"/><path d="M50 55 h6 M48 34 h10 M48 40 h10 M48 46 h10"/>
      </svg>
    </div>
    <span class="step-label">STEP 4</span><p>Lorem ipsum dolor sit amet, consectetur adipiscing elit, sed do eiusmod tempor inci didunt ut labore</p>
  </div>
  <div class="abs btn btn-teal" style="left:517px;top:1319px;width:166px;height:42px">DONATE DATA</div>
</section>

<section>
  <div class="abs donation"></div>
  <div class="abs glow" style="left:880px;top:1470px;width:240px;height:160px"></div>
  <div class="abs glow" style="left:80px;top:1890px;width:220px;height:120px"></div>
  <h2 class="abs center donation-title">MY DONATION</h2>
  <p class="abs center donation-note">ALL DONATION ARE TAX DEDUCTIBLE</p>
  <p class="abs center donation-want">I WANT TO GIVE</p>
  <div class="abs amounts">
    <div class="amount">$25</div><div class="amount">$50</div><div class="amount">$100</div><div class="amount">$125</div><div class="amount">$150</div><div class="amount other">OTHER<br>AMOUNT</div>
  </div>
  <div class="abs cards" aria-label="Accepted payment cards">
    <span class="card-shape"></span><span class="card-shape"></span><span class="card-shape"></span><span class="card-shape"></span><span class="card-shape"></span>
  </div>
  <div class="abs btn btn-teal" style="left:483px;top:1866px;width:234px;height:42px">DONATE WITH CREDIT CARD</div>
</section>

<section>
  <div class="abs donate-box" style="left:112px">
    <div class="donate-icon" aria-label="Crypto wallet icon">
      <svg width="64" height="64" viewBox="0 0 64 64" fill="none" stroke="#0a8f9b" stroke-width="2.5">
        <circle cx="32" cy="14" r="9"/><path d="M29 9 v10 M29 9 h4 q3 0 3 2.5 q0 2.5 -3 2.5 h-4 M29 14 h5 q3 0 3 2.5 q0 2.5 -3 2.5 h-5"/>
        <rect x="8" y="26" width="48" height="30" rx="4"/><rect x="40" y="35" width="16" height="12" rx="3"/><circle cx="46" cy="41" r="2"/>
        <path d="M14 34 h14 M14 42 h8 M14 50 h14"/>
      </svg>
    </div>
    <h3>DONATE WITH CRYPTO</h3><small>POWERED BY GWH</small>
    <div class="brand"><span class="brand-dot"></span>Giftwell Hub</div>
    <div class="btn btn-green">DONATE DATA</div>
  </div>
  <div class="abs donate-box" style="left:611px">
    <div class="donate-icon" aria-label="Data analysis icon">
      <svg width="64" height="64" viewBox="0 0 64 64" fill="none" stroke="#0a8f9b" stroke-width="2.5">
        <circle cx="38" cy="26" r="20"/><path d="M24 40 L8 56 l3 3 16 -16"/>
        <path d="M30 34 v-8 M36 34 v-14 M42 34 v-10 M48 34 v-16"/>
      </svg>
    </div>
    <h3>DONATE WITH DATA</h3><small>POWERED BY GWH</small>
    <div class="brand"><span class="brand-dot"></span>Giftwell Hub</div>
    <div class="btn btn-green">DONATE DATA</div>
  </div>
</section>

<div class="abs video" role="img" aria-label="Video still of a team working together around an office table"></div>
<div class="abs play"><svg width="20" height="22" viewBox="0 0 20 22"><path d="M2 1 L19 11 L2 21 Z" fill="#fff"/></svg></div>

<section>
  <div class="abs enroll"></div>
  <div class="abs notify"></div>
  <h2 class="abs enroll-title">WHY ENROLL!</h2>
  <div class="abs perk" style="top:3292px">
    <div class="perk-icon" aria-label="Drops icon">
      <svg width="44" height="44" viewBox="0 0 44 44" fill="none" stroke="#fff" stroke-width="2"><circle cx="22" cy="22" r="16" stroke-dasharray="4 4"/><circle cx="22" cy="24" r="8"/><path d="M22 6 v10 M18 12 l4 4 4 -4"/></svg>
    </div>
    <div><h4>DROPS</h4><p>Lorem ipsum dolor sit amet, consectetur cing<br>elit, sed do eiusmod tempor</p></div>
  </div>
  <div class="abs perk" style="top:3412px">
    <div class="perk-icon" aria-label="Marketplace icon">
      <svg width="44" height="44" viewBox="0 0 44 44" fill="none" stroke="#fff" stroke-width="2"><path d="M6 16 L10 6 H34 L38 16 Z M6 16 q4 5 8 0 q4 5 8 0 q4 5 8 0 q4 5 8 0"/><path d="M9 20 V38 H35 V20"/><rect x="13" y="25" width="8" height="13"/><rect x="25" y="25" width="7" height="6"/></svg>
    </div>
    <div><h4>MARKETPLACE</h4><p>Lorem ipsum dolor sit amet, consectetur cing<br>elit, sed do eiusmod tempor</p></div>
  </div>
  <div class="abs perk" style="top:3541px">
    <div class="perk-icon" aria-label="NFT icon">
      <svg width="48" height="48" viewBox="0 0 48 48" fill="none" stroke="#fff" stroke-width="2"><path d="M24 3 L42 13.5 V34.5 L24 45 L6 34.5 V13.5 Z"/><text x="24" y="29" text-anchor="middle" font-family="Poppins,sans-serif" font-size="12" fill="#fff" stroke="none" font-weight="500">NFT</text></svg>
    </div>
    <div><h4>MY NFTS</h4><p>Lorem ipsum dolor sit amet, consectetur cing<br>elit, sed do eiusmod tempor</p></div>
  </div>

  <h2 class="abs notify-title">GET NOTIFIED ABOUT<br>NEW AMAZING PRODUCTS</h2>
  <div class="abs subscribe">Email address<span class="btn">SUBSCRIBE</span></div>
  <p class="abs never">NEVER MISS A DROB</p>
  <p class="abs notify-text" style="top:3436px;font-size:14px">Subscribe for the latest news, Drop &amp; Collectibles</p>
  <p class="abs notify-text" style="top:3481px">Lorem ipsum dolor sit amet, consectetur adipiscing elit, sed do eiusmod tempor incididunt ut labore et dolore magna aliqua. Ut enim ad minim veniam, quis</p>
  <p class="abs notify-text" style="top:3584px">Nostrud exercitation ullamco laboris nisi ut aliquip</p>
</section>

<footer>
  <p class="abs center footer">© Copyrights 2022 Company name | All Rights Reserved</p>
  <span class="abs footer-code">C38</span>
</footer>

</body>
</html>
```